Modern Verdell Tree Care Website

I need a website for a full service Tree Care company. The company provides tree pruning, tree removal, tree preservation, emergency services, stump grinding, and emergency tree services.

Target Market(s)

Customers that need tree services

Industry/Entity Type

Landscaping, Tree Services

Coding

Coded - Design and coding required

Number of Pages Required

5+ page

Font styles to use
Sans Serif

Requirements
Must have
• Good clean design that showcases the services the company provides.
Nice to have
• Services page; contact form, blog, home page, about page

```html
<!DOCTYPE html>
<html lang="en">
<head>
<meta charset="utf-8">
<title>Verdell Tree Care</title>
<link rel="stylesheet" href="https://fonts.googleapis.com/css2?family=Ubuntu:wght@400;500;700&display=swap">
<style>
:root{
  --green:#86c24a;
  --green-dark:#6fae35;
  --orange:#f9aa38;
  --tan:#c49a6c;
  --ink:#141414;
  --grey:#7a7a7a;
  --line:#d6d6d6;
  --white:#fff;
}
*{margin:0;padding:0;box-sizing:border-box}
html,body{width:1200px;height:4257px;overflow:hidden}
body{font-family:"Ubuntu",sans-serif;color:var(--ink);background:var(--white);position:relative}
.abs{position:absolute}
.btn{position:absolute;background:var(--green);color:#fff;font-weight:500;display:flex;align-items:center;justify-content:center;font-size:20px}
.site-header{position:absolute;left:0;top:0;width:1200px;height:104px;background:#fff}
.brand{position:absolute;left:99px;top:34px;display:flex;align-items:center;gap:8px;font-size:19px;font-weight:700;color:var(--green);white-space:nowrap}
.brand-dot{width:26px;height:26px;background:var(--orange);flex:none}
.nav a{position:absolute;top:38px;font-size:17px;color:#444;text-decoration:none}
.hero{position:absolute;left:0;top:104px;width:1200px;height:540px;background:linear-gradient(110deg,#2a2217 0%,#4b3823 45%,#7a5632 70%,#3a2a1a 100%)}
.hero-kicker{position:absolute;left:102px;top:148px;color:#fff;font-size:24px}
.hero-title{position:absolute;left:102px;top:172px;color:var(--green);font-size:50px;font-weight:500;white-space:nowrap}
.hero-text{position:absolute;left:100px;top:244px;width:425px;color:#fff;font-size:14.5px;line-height:26px}
.badge{position:absolute;width:80px;height:80px;border-radius:50%;background:#fff;box-shadow:0 3px 8px rgba(0,0,0,.3);display:flex;align-items:center;justify-content:center}
.badge span{width:28px;height:28px;border-radius:50%;background:var(--green)}
.sec-ghost{position:absolute;font-size:58px;font-weight:700;color:rgba(0,0,0,.07);white-space:nowrap}
.sec-title{position:absolute;font-size:38px;font-weight:700;white-space:nowrap}
.rule{position:absolute;width:48px;height:4px;background:var(--orange)}
.center{left:0;width:1200px;text-align:center}
.lead{position:absolute;left:270px;width:660px;text-align:center;font-size:15px;line-height:25px}
.about-photo{position:absolute;left:145px;top:732px;width:419px;height:418px;background:linear-gradient(135deg,#4f7a2f,#8a6a45 55%,#2e4a1f)}
.about-text{position:absolute;left:653px;top:822px;width:448px;font-size:14.5px;line-height:25.7px;color:var(--grey)}
.services{position:absolute;left:0;top:1215px;width:1200px;height:915px;background:var(--green)}
.card{position:absolute;top:312px;width:322px;height:395px;background:#fff;border-radius:8px;padding:8px}
.card.active{background:var(--orange);color:#fff}
.card-img{width:306px;height:195px;border-radius:8px}
.card h3{font-size:26px;font-weight:500;margin:12px 4px 0}
.card p{font-size:14.5px;line-height:25px;color:var(--grey);margin:10px 6px 0}
.card.active p{color:#fff}
.card a{display:inline-block;margin:14px 8px 0;font-size:16px;font-weight:500;color:#2c5a16;text-decoration:underline}
.arrow{position:absolute;top:498px;width:30px;height:30px;border-radius:50%;background:#fff;display:flex;align-items:center;justify-content:center}
.field{position:absolute;border:1px solid var(--line);font-size:14px;color:#444;padding:0 20px;display:flex;align-items:center}
.blog{position:absolute;left:0;top:2918px;width:1200px;height:760px;background:var(--tan)}
.post{position:absolute;top:368px;height:342px;background:#fff;padding:10px}
.post h4{font-size:15px;font-weight:700;text-transform:uppercase;line-height:24px;margin:16px 8px 0}
.post p{font-size:14px;line-height:20px;margin:8px 8px 0}
.footer{position:absolute;left:0;top:3661px;width:1200px;height:596px;background:var(--ink);color:#fff}
.footer .brand{top:300px;font-size:27px;gap:12px}
.footer .brand-dot{width:38px;height:38px}
.f-head{position:absolute;top:213px;font-size:21px;font-weight:500}
.f-list{position:absolute;top:264px;list-style:none;font-size:16px;line-height:27.5px}
.f-item{position:absolute;left:894px;font-size:15px;line-height:23px}
.f-icon{position:absolute;left:864px}
</style>
</head>
<body>

<header class="site-header">
  <div class="brand"><span class="brand-dot"></span>Verdell Tree Care</div>
  <nav class="nav">
    <a style="left:329px">Home</a>
    <a style="left:410px">About Us</a>
    <a style="left:516px">Our Services</a>
    <a style="left:646px">Blog</a>
    <a style="left:716px">Contact Us</a>
  </nav>
  <div class="btn" style="left:846px;top:25px;width:245px;height:48px;font-size:20px">Call For Free Estimate</div>
</header>

<section class="hero" role="img" aria-label="Arborist in safety gear cutting a log with a chainsaw in a forest">
  <div class="hero-kicker">WELCOME TO</div>
  <h1 class="hero-title">Verdell Tree Care</h1>
  <p class="hero-text">Lorem ipsum dolor sit amet, consectetur adipiscing elit, sed do eiusmod tempor incididunt ut labore et dolore magna aliqua.</p>
  <div class="btn" style="left:102px;top:337px;width:164px;height:50px">Get Started</div>
</section>
<svg class="abs" style="left:0;top:540px" width="1200" height="110" viewBox="0 0 1200 110">
  <polygon points="0,100 600,40 1200,100 1200,110 0,110" fill="#fff"/>
  <polyline points="0,92 600,32 1200,92" fill="none" stroke="#f9aa38" stroke-width="10"/>
</svg>
<div class="badge" style="left:563px;top:544px"><span></span></div>

<section>
  <div class="about-photo" role="img" aria-label="Arborist cutting a tree trunk, framed in a triangular shape"></div>
  <div class="sec-ghost" style="left:663px;top:712px">ABOUT US</div>
  <h2 class="sec-title" style="left:661px;top:745px">ABOUT US</h2>
  <div class="rule" style="left:661px;top:797px"></div>
  <p class="about-text">Sed ut perspiciatis unde omnis iste natus error sit voluptatem accusantium doloremque laudantium, totam rem aperiam, eaque ipsa quae ab illo inventore veritatis et quasi architecto beatae vitae dicta sunt explicabo. Nemo enim ipsam voluptatem quia voluptas sit aspernatur aut odit aut fugit, sed quia consequuntur magni dolores eos qui ratione voluptatem sequi nesciunt. Sed ut perspiciatis unde omnis iste natus error sit voluptatem accusantium doloremque laudantium, totam rem aperiam, eaque ipsa quae ab illo inventore veritatis et quasi</p>
  <div class="btn" style="left:653px;top:1083px;width:162px;height:49px">Read More</div>
</section>

<section class="services">
  <svg class="abs" style="left:0;top:0" width="1200" height="110" viewBox="0 0 1200 110">
    <polygon points="0,0 1200,0 1200,2 600,92 0,2" fill="#fff"/>
    <polyline points="0,10 600,100 1200,10" fill="none" stroke="#f9aa38" stroke-width="9"/>
  </svg>
  <div class="sec-ghost center" style="top:118px;color:rgba(0,0,0,.08);font-size:74px">OUR SERVICES</div>
  <h2 class="sec-title center" style="top:163px">OUR SERVICES</h2>
  <p class="lead" style="top:227px">Lorem ipsum dolor sit amet, consectetur adipiscing elit, sed do eiusmod tempor incididunt ut labore et dolore magna aliqua.</p>
  <div class="arrow" style="left:46px"><svg width="18" height="18" viewBox="0 0 18 18"><path d="M15 9H4M8 4L3 9l5 5" stroke="#6fae35" stroke-width="2.5" fill="none"/></svg></div>
  <div class="arrow" style="left:1122px"><svg width="18" height="18" viewBox="0 0 18 18"><path d="M3 9h11M10 4l5 5-5 5" stroke="#6fae35" stroke-width="2.5" fill="none"/></svg></div>
  <article class="card" style="left:101px">
    <div class="card-img" role="img" aria-label="Pruning shears cutting a branch" style="background:linear-gradient(135deg,#9bbf6a,#6b8a48)"></div>
    <h3>Tree Pruning</h3>
    <p>Lorem ipsum dolor sit amet, consectetur adipiscing elit, sed do eiusmod tempor incididunt ut labore et</p>
    <a>Read More</a>
  </article>
  <article class="card active" style="left:440px">
    <div class="card-img" role="img" aria-label="Worker cutting a tree stump with a chainsaw" style="background:linear-gradient(135deg,#a89274,#5f6b3c)"></div>
    <h3>Tree Removal</h3>
    <p>Lorem ipsum dolor sit amet, consectetur adipiscing elit, sed do eiusmod tempor incididunt ut labore et</p>
    <a>Read More</a>
  </article>
  <article class="card" style="left:779px">
    <div class="card-img" role="img" aria-label="Volunteers planting young trees in soil" style="background:linear-gradient(135deg,#5b6f55,#2f3d2c)"></div>
    <h3>Tree Preservation</h3>
    <p>Lorem ipsum dolor sit amet, consectetur adipiscing elit, sed do eiusmod tempor incididunt ut labore et</p>
    <a>Read More</a>
  </article>
  <svg class="abs" style="left:0;top:735px" width="1200" height="180" viewBox="0 0 1200 180">
    <polygon points="0,30 600,160 1200,30 1200,180 0,180" fill="#fff"/>
    <polyline points="0,20 600,150 1200,20" fill="none" stroke="#f9aa38" stroke-width="10"/>
  </svg>
</section>

<section>
  <div class="sec-ghost center" style="top:2200px;font-size:64px">CONTACT FORM</div>
  <h2 class="sec-title center" style="top:2240px">CONTACT FORM</h2>
  <div class="rule" style="left:553px;top:2297px"></div>
  <p class="lead" style="top:2318px">Lorem ipsum dolor sit amet, consectetur adipiscing elit, sed do eiusmod tempor incididunt ut labore et dolore magna aliqua.</p>
  <div class="field" style="left:182px;top:2402px;width:408px;height:59px">First Name</div>
  <div class="field" style="left:612px;top:2402px;width:408px;height:59px">Last Name</div>
  <div class="field" style="left:182px;top:2488px;width:408px;height:59px">Phone Number</div>
  <div class="field" style="left:612px;top:2488px;width:408px;height:59px">Email</div>
  <div class="field" style="left:182px;top:2580px;width:838px;height:190px;align-items:flex-start;padding-top:20px">Messages</div>
  <div class="btn" style="left:519px;top:2808px;width:162px;height:49px">Send Now</div>
</section>

<section class="blog">
  <svg class="abs" style="left:0;top:0" width="1200" height="120" viewBox="0 0 1200 120">
    <polygon points="0,0 1200,0 1200,20 600,100 0,20" fill="#fff"/>
    <polyline points="0,30 600,110 1200,30" fill="none" stroke="#f9aa38" stroke-width="10"/>
  </svg>
  <div class="sec-ghost center" style="top:172px;color:rgba(0,0,0,.08);font-size:64px">OUR LATEST NEWS</div>
  <h2 class="sec-title center" style="top:206px;color:#fff">OUR BLOG</h2>
  <div class="rule" style="left:553px;top:260px"></div>
  <p class="lead" style="top:295px;color:#fff">Lorem ipsum dolor sit amet, consectetur adipiscing elit, sed do eiusmod tempor incididunt ut labore et dolore magna aliqua.</p>
  <article class="post" style="left:101px;width:438px">
    <div role="img" aria-label="Crew feeding branches into a wood chipper" style="height:189px;background:linear-gradient(135deg,#7ea24f,#4d6b33 60%,#8c8c8c)"></div>
    <h4>Nemo enim ipsam voluptatem</h4>
    <p>Lorem ipsum dolor sit amet, consectetur adipiscing elit, sed do eiusmod tempor incididunt ut labore et dolore magna aliqua.</p>
  </article>
  <article class="post" style="left:555px;width:265px">
    <div role="img" aria-label="Climber cutting branches high in a tree" style="height:253px;background:linear-gradient(160deg,#7aa6d6,#5b5146 60%,#3f4a2c)"></div>
    <h4>Nemo enim ipsam voluptatem</h4>
  </article>
  <article class="post" style="left:835px;width:266px">
    <div role="img" aria-label="Gloved hands sawing a tree trunk" style="height:253px;background:linear-gradient(135deg,#5c7a45,#8a8476 50%,#3a4f2b)"></div>
    <h4>Nemo enim ipsam voluptatem</h4>
  </article>
</section>

<footer class="footer">
  <svg class="abs" style="left:0;top:0" width="1200" height="150" viewBox="0 0 1200 150">
    <polygon points="0,0 1200,0 1200,10 600,120 0,10" fill="#c49a6c"/>
    <polyline points="0,22 600,132 1200,22" fill="none" stroke="#f9aa38" stroke-width="10"/>
  </svg>
  <div class="badge" style="left:563px;top:92px"><span></span></div>
  <div class="brand"><span class="brand-dot"></span>Verdell Tree Care</div>
  <div class="f-head" style="left:446px">QUICK LINKS</div>
  <ul class="f-list" style="left:446px"><li>Home</li><li>About Us</li><li>Our Services</li><li>Blog</li><li>Contact Us</li></ul>
  <div class="f-head" style="left:655px">USEFUL LINKS</div>
  <ul class="f-list" style="left:655px"><li>Terms &amp; Conditions</li><li>Privacy Policy</li><li>About Us</li><li>Support</li></ul>
  <div class="f-head" style="left:865px">CONTACT US</div>
  <svg class="f-icon" style="top:265px" width="14" height="18" viewBox="0 0 14 18"><path d="M7 0a6 6 0 0 0-6 6c0 5 6 12 6 12s6-7 6-12a6 6 0 0 0-6-6zm0 8.5A2.5 2.5 0 1 1 7 3.5a2.5 2.5 0 0 1 0 5z" fill="#fff"/></svg>
  <div class="f-item" style="top:263px;width:190px">Lorem ipsum dolor sit amet, consectetur adipiscing</div>
  <svg class="f-icon" style="top:360px" width="16" height="16" viewBox="0 0 16 16"><path d="M3 1l3 3-2 2c1 2 3 4 5 5l2-2 3 3-2 3C7 15 1 9 1 3z" fill="#fff"/></svg>
  <div class="f-item" style="top:356px">+1 555 014-2739</div>
  <svg class="f-icon" style="top:409px" width="16" height="12" viewBox="0 0 16 12"><rect width="16" height="12" rx="1" fill="#fff"/><path d="M1 1l7 6 7-6" stroke="#141414" stroke-width="1.5" fill="none"/></svg>
  <div class="f-item" style="top:403px;font-size:13px">info@verdelltreecare.com</div>
  <div class="abs" style="left:102px;top:500px;font-size:16px">© 2024 Verdell Tree care. All Rights Reserved.</div>
</footer>

</body>
</html>
```